Valdane Companies Business Card Design

We need a new business card for our Private Equity Real Estate Development firm, “Valdane” and our EB-5 regional center “Thornmere Regional Center” on one card. We prefer a design that is simple, elegant, and represents the luxury products we design and build as well as the financial security and stability our successful history has produced. We are an industry leader in our field and 3rd generation family business that has evolved into an institutional quality investment platform. Considered design size is standard business card dimensions (3.5 x 2 inches with an additional 1/8 inch space for design elements or backgrounds that extend beyond the finished size of your piece.

Target Market(s)

• High net worth individuals
• Highly skilled technical workers and physicians in the US seeking investment-based immigration opportunities
• Sophisticated private equity investors
• Intermediary partners include domestic attorneys and investment brokers, as well as international agent networks
• US real estate developers

Industry/Entity Type

Finance

Contact Information for Business Card

(Providing placeholder info for personal information, please design for longer character spaces, longer names and addresses etc..)
• Logo for Valdane
• Logo for Thornmere Regional Center
• Full name: Marcus Valdane
• Job title: CEO
• Email address: mvaldane@valdanecompanies.com
• Cell phone number: +1.555.314.2287
• Office number +1.555.628.4410
• Office address: Larkfield Court 5, 4817 Vista Orilla, Alderbrook, OR.
• Website: www.valdanecompanies.com

Font styles to use
Serif
Sans Serif

Colors
ec1f27
ffffff
000000

Requirements
Must have
• • Logo for Valdane
• • Logo for Thornmere Regional Center
• - Use rounded corners
• (See .ai file included for logos)
Nice to have
• • Simple, elegant design
• • Aesthetically compatible with our website design (www.valdanecompanies.com)
• • Color palette including but not limited to white, black, and red (as per logos)
Should not have
• - Not too much red color
• - Do not stack both logos on top of each other

```html
<!DOCTYPE html>
<html lang="en">
<head>
<meta charset="utf-8">
<title>Valdane Companies Business Card</title>
<link rel="stylesheet" href="https://fonts.googleapis.com/css2?family=Cinzel:wght@700&family=Tinos&display=swap">
<style>
  :root {
    --stage: #3a3a3c;
    --card-white: #ffffff;
    --card-black: #0d0d0d;
    --brand-red: #a51c2e;
    --ink: #111111;
    --ink-soft: #2a2a2a;
    --emboss: #2c2c2c;
  }
  * { margin: 0; padding: 0; box-sizing: border-box; }
  html, body {
    width: 1200px;
    height: 1000px;
    overflow: hidden;
    background: var(--stage);
  }
  .stage {
    position: relative;
    width: 1200px;
    height: 1000px;
  }
  .card {
    position: absolute;
    left: 250px;
    width: 700px;
    height: 400px;
    border-radius: 28px;
    overflow: hidden;
  }
  .card-back {
    top: 50px;
    background: var(--card-black);
  }
  .card-front {
    top: 530px;
    background: var(--card-white);
  }

  /* back */
  .back-brand {
    position: absolute;
    inset: 0;
    display: flex;
    align-items: center;
    justify-content: center;
    font-family: "Cinzel", serif;
    font-weight: 700;
    font-size: 52px;
    letter-spacing: 2px;
    color: var(--emboss);
    text-align: center;
  }

  /* front */
  .front-brand {
    position: absolute;
    left: 56px;
    top: 60px;
    font-family: "Cinzel", serif;
    font-weight: 700;
    font-size: 38px;
    letter-spacing: 1px;
    line-height: 1;
    color: var(--ink);
  }

  .accent-bar {
    position: absolute;
    background: var(--brand-red);
  }
  .accent-bar.left { left: 0; top: 190px; width: 28px; height: 120px; }
  .accent-bar.right { right: 0; top: 168px; width: 30px; height: 48px; }

  .contact {
    position: absolute;
    left: 50px;
    top: 192px;
    font-family: "Tinos", serif;
    font-size: 17px;
    line-height: 22px;
    color: var(--ink-soft);
    list-style: none;
  }
  .contact li { display: flex; align-items: center; gap: 8px; }
  .contact .address { padding-left: 20px; }
  .contact svg { width: 12px; height: 12px; flex: none; fill: var(--brand-red); }
  .contact .web-accent { color: var(--brand-red); }

  .person {
    position: absolute;
    right: 44px;
    top: 166px;
    text-align: right;
  }
  .person .name {
    font-family: "Cinzel", serif;
    font-weight: 700;
    font-size: 26px;
    color: var(--brand-red);
    line-height: 1.1;
  }
  .person .title {
    font-family: "Tinos", serif;
    font-size: 15px;
    color: var(--ink);
    margin-top: 2px;
  }

  .center-brand {
    position: absolute;
    right: 40px;
    bottom: 46px;
    display: flex;
    align-items: center;
    gap: 12px;
  }
  .center-brand .mark {
    width: 26px;
    height: 26px;
    background: var(--brand-red);
  }
  .center-brand .center-name {
    font-family: "Cinzel", serif;
    font-weight: 700;
    font-size: 20px;
    color: var(--brand-red);
  }
</style>
</head>
<body>
<main class="stage">

  <section class="card card-back" aria-label="Card back">
    <div class="back-brand">VALDANE CAPITAL</div>
  </section>

  <section class="card card-front" aria-label="Card front">
    <div class="front-brand">VALDANE CAPITAL</div>

    <div class="accent-bar left"></div>
    <div class="accent-bar right"></div>

    <ul class="contact">
      <li class="address">Larkfield Court 5, 4817</li>
      <li class="address">Vista Orilla, Alderbrook, OR.</li>
      <li>
        <svg viewBox="0 0 12 12" aria-hidden="true"><path d="M2.5 1h2l1 3-1.4 1a6 6 0 0 0 2.9 2.9l1-1.4 3 1v2a1.5 1.5 0 0 1-1.5 1.5A9.5 9.5 0 0 1 1 2.5 1.5 1.5 0 0 1 2.5 1z"/></svg>
        +1.555.314.2287
      </li>
      <li>
        <svg viewBox="0 0 12 12" aria-hidden="true"><path d="M3 0h6a1 1 0 0 1 1 1v10a1 1 0 0 1-1 1H3a1 1 0 0 1-1-1V1a1 1 0 0 1 1-1zm0 1.5v8h6v-8z"/></svg>
        +1.555.628.4410
      </li>
      <li>
        <svg viewBox="0 0 12 12" aria-hidden="true"><path d="M0 2h12v8H0zM1 3v.3l5 3.2 5-3.2V3z"/></svg>
        mvaldane@valdanecompanies.com
      </li>
      <li>
        <svg viewBox="0 0 12 12" aria-hidden="true"><circle cx="6" cy="6" r="6"/></svg>
        <span>www.<span class="web-accent">valdanecompanies</span>.com</span>
      </li>
    </ul>

    <div class="person">
      <div class="name">MARCUS VALDANE</div>
      <div class="title">CEO</div>
    </div>

    <div class="center-brand">
      <div class="mark"></div>
      <div class="center-name">Thornmere Regional Center</div>
    </div>
  </section>

</main>
</body>
</html>
```